Antiseptic products for Verolin East Africa

I need several antiseptic product designs for topical solutions such as surgical spirit, methylated spirit, hand sanitizer, calamine lotion, povidone solution, glycerine, povidone mouthwash, chlorhexidine solution, and sodium hypochlorite solution.

KINDLY START WITH THE HAND SANITIZER DESIGN, URGENT.

Target Market(s)

International market

Industry/Entity Type

Pharmaceutical

Font styles to use
Serif
Script

Colors
33a6d7
3277b5
0758a5
7651a1
886aae
e34197
e667a6
f78f20

Requirements
Must have
• Elegant designs, writtings to appear as they are. safety symbols to appear such as flammable or corrosive.
Nice to have
• Attractive colours but keep it simple and classy.

```html
<!DOCTYPE html>
<html lang="en">
<head>
<meta charset="utf-8">
<title>Verolin East Africa – Product Labels</title>
<link rel="stylesheet" href="https://fonts.googleapis.com/css2?family=Montserrat:wght@400;500;600;700;800&family=Encode+Sans+Condensed:wght@400;500&display=swap">
<style>
  :root {
    --bg: #ececec;
    --label-white: #f7f7f8;
    --purple: #7d5bb3;
    --purple-light: #9a7cc9;
    --ink-grey: #6c6c70;
    --brand-slate: #4a5866;
    --brand-blue: #3d8cc9;
    --fresh-green: #8dc63f;
    --charcoal: #3b3b3e;
    --lime: #d6df23;
    --lime-light: #e3ea5a;
    --tan: #c8b27c;
    --light-text: #ececec;
    --dark-text: #2c2c2c;
  }
  * { box-sizing: border-box; margin: 0; padding: 0; }
  html, body { width: 1200px; height: 1200px; overflow: hidden; }
  body {
    background: radial-gradient(circle at 50% 45%, #f7f7f7 0%, var(--bg) 75%);
    font-family: "Montserrat", sans-serif;
    position: relative;
  }
  .label { position: absolute; overflow: hidden; border-radius: 10px; }
  .label > * { position: absolute; }

  /* Sanitizer label */
  .sanitizer { left: 284px; top: 383px; width: 350px; height: 700px; background: var(--label-white); }
  .brand { display: flex; align-items: center; gap: 7px; white-space: nowrap; font-weight: 600; letter-spacing: 2px; font-size: 15px; }
  .sanitizer .brand { left: 0; right: 0; top: 78px; justify-content: center; color: var(--brand-slate); }
  .brand .dot { width: 14px; height: 14px; border-radius: 50%; }
  .sanitizer .brand .dot { background: var(--brand-blue); }
  .sanitizer .heart { left: 238px; top: 150px; width: 26px; height: 24px; }
  .product-name { left: 19px; width: 312px; top: 176px; font-size: 62px; font-weight: 800; color: var(--purple); text-align: right; letter-spacing: -1px; line-height: 1.1; }
  .rule { height: 1.5px; background: var(--purple); }
  .sanitizer .rule-top { left: 111px; width: 220px; top: 267px; }
  .sanitizer .rule-bottom { left: 111px; width: 220px; top: 370px; }
  .descriptor { right: 19px; top: 270px; text-align: right; font-family: "Encode Sans Condensed", sans-serif; color: var(--ink-grey); font-size: 44px; line-height: 46px; }
  .no-germs { left: 177px; top: 394px; width: 60px; height: 60px; }
  .claim { right: 19px; top: 378px; text-align: right; color: var(--ink-grey); }
  .claim .kill { font-size: 42px; font-weight: 800; line-height: 44px; }
  .claim .pct { font-size: 21px; font-weight: 700; line-height: 24px; }
  .claim .small { font-size: 18px; font-weight: 500; line-height: 24px; letter-spacing: .5px; }
  .purple-band { left: 0; bottom: 0; width: 350px; height: 200px; }
  .fresh-seal { left: 63px; top: 523px; width: 100px; height: 100px; border-radius: 50%; background: var(--fresh-green); border: 4px solid #fff; color: #fff; font-size: 13px; font-weight: 600; display: flex; align-items: center; justify-content: center; text-align: center; line-height: 15px; }
  .maker { font-size: 10px; line-height: 12px; }
  .sanitizer .maker { left: 27px; top: 634px; color: #fff; }
  .maker b { font-weight: 700; }
  .volume-text { right: 26px; top: 650px; color: #fff; font-size: 26px; font-weight: 700; }

  /* Castor oil label */
  .castor { left: 734px; top: 366px; width: 296px; height: 690px; background: var(--charcoal); }
  .castor .brand { left: 0; right: 0; top: 86px; justify-content: center; color: var(--light-text); }
  .castor .brand .dot { background: var(--lime); }
  .eyebrow { left: 0; right: 0; top: 150px; text-align: center; color: #c9c9c9; font-size: 13px; letter-spacing: 8px; padding-left: 8px; }
  .castor-word { left: 0; right: 0; text-align: center; color: var(--lime); font-weight: 800; line-height: 1; white-space: nowrap; }
  .castor-word.line1 { top: 174px; font-size: 58px; letter-spacing: -1.5px; }
  .castor-word.line2 { top: 264px; font-size: 74px; letter-spacing: -1px; }
  .castor .heart { left: 139px; top: 245px; width: 18px; height: 16px; }
  .grade { left: 0; right: 0; top: 346px; text-align: center; color: var(--tan); font-size: 16px; font-weight: 700; }
  .use-pill { left: 62px; top: 373px; width: 175px; height: 22px; border-radius: 11px; background: var(--lime); color: var(--dark-text); font-size: 13px; font-weight: 500; text-align: center; line-height: 22px; }
  .benefit { left: 19px; top: 408px; color: #f0f0f0; font-size: 15px; font-weight: 800; line-height: 19px; letter-spacing: -.3px; }
  .castor .rule { background: #d0d0d0; height: 1px; left: 19px; width: 150px; }
  .castor .rule-a { top: 455px; }
  .castor .rule-b { top: 510px; }
  .notes { left: 19px; color: #e0e0e0; font-size: 12.5px; line-height: 16px; }
  .notes.caution { top: 459px; }
  .notes.storage { top: 514px; }
  .lime-band { left: 0; bottom: 0; width: 296px; height: 150px; }
  .volume-badge { left: 224px; top: 540px; width: 60px; height: 60px; border-radius: 50%; background: var(--charcoal); border: 2px solid #bdbdbd; color: #d8d8d8; font-size: 15px; font-weight: 700; line-height: 15px; display: flex; align-items: center; justify-content: center; text-align: center; }
  .batch { left: 19px; top: 598px; color: var(--dark-text); font-size: 12px; line-height: 23px; }
  .castor .maker { right: 12px; top: 620px; text-align: right; color: var(--dark-text); }
</style>
</head>
<body>

  <section class="label sanitizer">
    <div class="brand"><span class="dot"></span>VEROLIN EAST AFRICA</div>
    <svg class="heart" viewBox="0 0 26 24" aria-hidden="true"><path d="M13 23 C3 15 0 11 0 7 A6.5 6.5 0 0 1 13 5 A6.5 6.5 0 0 1 26 7 C26 11 23 15 13 23Z" fill="#8a8f9c"/></svg>
    <h1 class="product-name">CLENORA</h1>
    <div class="rule rule-top"></div>
    <p class="descriptor">Instant Hand<br>Sanitizer</p>
    <div class="rule rule-bottom"></div>
    <svg class="no-germs" viewBox="0 0 60 60" aria-hidden="true"><circle cx="30" cy="30" r="27" fill="none" stroke="#8a8a8e" stroke-width="4"/><line x1="11" y1="11" x2="49" y2="49" stroke="#8a8a8e" stroke-width="4"/></svg>
    <div class="claim">
      <div class="kill">Kill</div>
      <div class="pct">99.99%</div>
      <div class="small">of germs</div>
      <div class="small">without water</div>
    </div>
    <svg class="purple-band" viewBox="0 0 350 200" preserveAspectRatio="none" role="img" aria-label="Purple bubble pattern rising from the bottom of the label">
      <defs>
        <linearGradient id="purpleFade" x1="0" y1="0" x2="0" y2="1">
          <stop offset="0" stop-color="var(--purple-light)" stop-opacity="0"/>
          <stop offset="0.3" stop-color="var(--purple-light)" stop-opacity="0.6"/>
          <stop offset="0.45" stop-color="var(--purple)"/>
          <stop offset="1" stop-color="var(--purple)"/>
        </linearGradient>
      </defs>
      <path d="M0 0 L350 0 L350 200 L0 200Z" fill="url(#purpleFade)"/>
    </svg>
    <div class="fresh-seal">with natural<br>fresh smell</div>
    <p class="maker">Mfd. by:<br><b>Verolin EA</b><br>452 - 20300 Kenya</p>
    <div class="volume-text">200mL</div>
  </section>

  <section class="label castor">
    <div class="brand"><span class="dot"></span>VEROLIN EAST AFRICA</div>
    <div class="eyebrow">NATURAL</div>
    <div class="castor-word line1">CASTOR</div>
    <svg class="heart" viewBox="0 0 26 24" aria-hidden="true"><path d="M13 23 C3 15 0 11 0 7 A6.5 6.5 0 0 1 13 5 A6.5 6.5 0 0 1 26 7 C26 11 23 15 13 23Z" fill="#ffffff"/></svg>
    <div class="castor-word line2">OIL</div>
    <div class="grade">Medicinal Castor Oil BP</div>
    <div class="use-pill">For Oral &amp; Topical Use</div>
    <p class="benefit">GREAT MOISTURIZING<br>&amp; HEALING OIL</p>
    <div class="rule rule-a"></div>
    <p class="notes caution">CAUTION:<br>KEEP OUT OF<br>REACH OF CHILDREN</p>
    <div class="rule rule-b"></div>
    <p class="notes storage">STORAGE<br>Store in a cool dry place</p>
    <svg class="lime-band" viewBox="0 0 296 150" preserveAspectRatio="none" role="img" aria-label="Lime bubble pattern rising from the bottom of the label">
      <defs>
        <linearGradient id="limeFade" x1="0" y1="0" x2="0" y2="1">
          <stop offset="0" stop-color="var(--lime-light)" stop-opacity="0"/>
          <stop offset="0.25" stop-color="var(--lime-light)" stop-opacity="0.6"/>
          <stop offset="0.4" stop-color="var(--lime)"/>
          <stop offset="1" stop-color="var(--lime)"/>
        </linearGradient>
      </defs>
      <path d="M0 0 L296 0 L296 150 L0 150Z" fill="url(#limeFade)"/>
    </svg>
    <div class="volume-badge">150<br>mL</div>
    <p class="batch">B. No:<br>Mfg date:<br>Exp date:</p>
    <p class="maker">Mfd. by:<br><b>Verolin EA</b><br>1452 - 20300 Kenya</p>
  </section>

</body>
</html>
```